Korvile

I'd like new business card design options. I'll need to provide updated contact info although after the deign is complete. We are in IT, specifically in the data backup, archiving and disaster recovery verticals.

Industry/Entity Type

Business

```html
<!DOCTYPE html>
<html lang="en">
<head>
<meta charset="utf-8">
<title>Korvile business card</title>
<link rel="stylesheet" href="https://fonts.googleapis.com/css2?family=Montserrat:wght@600;800&family=Roboto+Condensed:wght@400;700&display=swap">
<style>
  :root {
    --stage: #e9ecef;
    --paper: #ffffff;
    --paper-shade: #eef0f2;
    --brand-blue: #0a6cc4;
    --brand-deep: #0756a8;
    --brand-sky: #2fa8e0;
    --brand-cyan: #36b6e6;
    --ink-light: #ffffff;
  }
  * { box-sizing: border-box; margin: 0; padding: 0; }
  html, body {
    width: 1200px; height: 780px; overflow: hidden;
    background: var(--stage);
  }
  .stage {
    position: relative; width: 1200px; height: 780px;
    display: flex; align-items: center; justify-content: center; gap: 40px;
  }
  .card {
    position: relative; width: 560px; height: 320px; overflow: hidden;
    border-radius: 4px;
    box-shadow: 0 6px 18px rgba(0,0,0,.18);
  }

  /* Front */
  .card-front {
    background: linear-gradient(180deg, var(--paper) 0%, var(--paper-shade) 100%);
  }
  .front-brand {
    position: absolute; left: 40px; top: 52px;
    display: flex; align-items: center; gap: 16px;
  }
  .brand-dot {
    width: 58px; height: 58px; border-radius: 50%;
    background: var(--brand-sky);
  }
  .brand-name {
    font-family: "Montserrat", sans-serif; font-weight: 800;
    font-size: 40px; letter-spacing: 6px; line-height: 1;
    color: var(--brand-blue);
  }
  .brand-tagline {
    font-family: "Montserrat", sans-serif; font-weight: 600;
    font-size: 13px; letter-spacing: 2px; margin-top: 6px;
    color: var(--brand-sky);
  }
  .name-strip {
    position: absolute; left: 0; right: 0; top: 168px; height: 32px;
    background: var(--brand-cyan);
    display: flex; align-items: center; padding-left: 40px;
    font-family: "Roboto Condensed", sans-serif; color: var(--ink-light);
  }
  .person-name { font-weight: 700; font-size: 17px; letter-spacing: .5px; }
  .divider { margin: 0 12px; opacity: .8; font-size: 17px; }
  .person-role { font-size: 15px; letter-spacing: .5px; }
  .contact-band {
    position: absolute; left: 0; right: 0; top: 200px; bottom: 0;
    background: linear-gradient(180deg, var(--brand-blue) 0%, var(--brand-deep) 100%);
    padding: 12px 40px 0 40px;
    font-family: "Roboto Condensed", sans-serif; font-size: 14.5px;
    line-height: 20px; color: var(--ink-light);
  }
  .contact-line { display: flex; align-items: center; gap: 6px; }
  .contact-line svg { width: 14px; height: 14px; flex: none; }
  .phone-gap { width: 14px; }

  /* Back */
  .card-back {
    background: radial-gradient(ellipse at 45% 35%, #1a86da 0%, var(--brand-blue) 45%, var(--brand-deep) 100%);
  }
  .back-brand {
    position: absolute; left: 0; right: 0; top: 100px;
    display: flex; align-items: center; justify-content: center; gap: 16px;
  }
  .card-back .brand-dot { background: var(--brand-sky); border: 2px solid rgba(255,255,255,.6); }
  .card-back .brand-name, .card-back .brand-tagline { color: var(--ink-light); }
  .service-line {
    position: absolute; left: 0; right: 0; bottom: 40px; text-align: center;
    font-family: "Roboto Condensed", sans-serif; font-size: 14px;
    letter-spacing: .5px; color: var(--ink-light);
  }
</style>
</head>
<body>
<main class="stage">
  <section class="card card-front" aria-label="Card front">
    <div class="front-brand">
      <span class="brand-dot"></span>
      <div>
        <div class="brand-name">KORVILE</div>
        <div class="brand-tagline">Your Steady Backup Partner</div>
      </div>
    </div>
    <div class="name-strip">
      <span class="person-name">DANIEL R. HOLLIS, Ph.D.</span>
      <span class="divider">|</span>
      <span class="person-role">PRESIDENT, CTO</span>
    </div>
    <div class="contact-band">
      <div class="contact-line">204 North Alder Street</div>
      <div class="contact-line">Brookfield, Texas 75210</div>
      <div class="contact-line">
        <svg viewBox="0 0 14 14" aria-hidden="true"><circle cx="7" cy="7" r="7" fill="#fff"/><rect x="3.5" y="4.5" width="7" height="5" fill="none" stroke="#0a6cc4" stroke-width="1"/><path d="M3.5 4.5 L7 7.5 L10.5 4.5" fill="none" stroke="#0a6cc4" stroke-width="1"/></svg>
        daniel.hollis@korvile.com
      </div>
      <div class="contact-line">
        <svg viewBox="0 0 14 14" aria-hidden="true"><circle cx="7" cy="7" r="7" fill="#fff"/><path d="M4.6 3.6 L6 5.4 L5.2 6.3 Q6.2 8 7.7 8.8 L8.6 8 L10.4 9.4 L9.5 10.6 Q6.5 10.4 3.6 4.5 Z" fill="#0a6cc4"/></svg>
        800.555.0142
        <span class="phone-gap"></span>
        <svg viewBox="0 0 14 14" aria-hidden="true"><circle cx="7" cy="7" r="7" fill="#fff"/><rect x="4" y="3.5" width="6" height="2.5" fill="#0a6cc4"/><rect x="3" y="6.5" width="8" height="4" rx="1" fill="#0a6cc4"/></svg>
        928.555.0187
      </div>
      <div class="contact-line">www.korvile.com</div>
    </div>
  </section>

  <section class="card card-back" aria-label="Card back">
    <div class="back-brand">
      <span class="brand-dot"></span>
      <div>
        <div class="brand-name">KORVILE</div>
        <div class="brand-tagline">Your Steady Backup Partner</div>
      </div>
    </div>
    <p class="service-line">ONLINE PC BACKUP • CONTINUOUS SERVER BACKUP • DATA ARCHIVING</p>
  </section>
</main>
</body>
</html>
```